Pull Up Banner - Recruitment Company

We would like a design for a pull up banner.

For context: we are a recruitment business. We specialise in helping people in healthcare industry to find jobs in Australia.

I have come up with several ideas and text for the banner. Feel free to use the following as you see appropriate:

- Our logo (see attached)
- 'Healthcare Recruitment Agency'
- Some sort of imagine / cartoon of medical professionals (ie. doctor, nurse, physiotherapist, speech pathologist). A cartoon is more friendly than committing to a photo
- 'Empowering your next career move'
- 'Discover tailored opportunities based on your career preferences'
- Dot points (allied health, nursing, medical imaging)
- Contact info at the bottom including our website (www.quellastaffing.com.au, our Instagram handle @quellastaffing, Mobile: XXXX XXX XXX. The title section for contact information could be 'Get in touch:'

Feel free to submit a couple of designs and we can merge aspects that look good on your designs and find the perfect fit.
Thank you
Updates

Hello,

Thank you for your initial submissions to this project. I appreciate the time you've invested.

After reviewing the first attempt, I'd like to share some feedback and initial observations:

- Professionalism and engagement: Is the overall appearance of the banner professional? It's crucial that we have a high-quality design as this will represent our business.

- Image selection: The image (whether cartoon or real people) appears quite generic. Please consider submitting the banner with a few different photos in the middle for us to choose from. Ensure the image is a good fit and not simply a generic stock photo.

- Contact section: Kindly remove the phone number; we no longer wish to include it on the banner. Instead, please include our website (www.quellastaffing.com.au) and Instagram handle (@quellastaffing).

- Color scheme: White, black, and red/pink are preferred, or alternatively, blue. However, please avoid incorporating too many different colors as it may detract from the professional appearance.

We will be printing the design on a banner and require it to look professional and engaging.

Thank you once again for your submissions. I hope the feedback provided above is helpful.

Warm regards,

Target Market(s)

Allied Health Australia

Font styles to use
Serif

Colors
0054AA
0677BA
7BADD7
CADEEF
E8F1F8
0094D4
00A9DD
6FCCEA
C7EBF8
E9F6FB
EB3D1F
EC4F4E
F09395
F8D3D4
FCEDEE

```html
<!DOCTYPE html>
<html lang="en">
<head>
<meta charset="utf-8">
<title>Quella Staffing – Healthcare Recruitment Pull Up Banner</title>
<link rel="stylesheet" href="https://fonts.googleapis.com/css2?family=Anton&family=Poppins:wght@400;600;700;800&display=swap">
<style>
  :root {
    --stage: #b4b4b4;
    --paper: #ffffff;
    --ink: #0d0d0d;
    --brand-blue: #2130c4;
    --panel-light: #bfe6f5;
    --panel-mid: #8fd0ea;
    --ring: #1c2450;
    --art-top: #e3f1f8;
    --art-mid: #a9d6ea;
    --art-low: #7cc6df;
    --footer: #1b1b1b;
  }
  * { box-sizing: border-box; margin: 0; padding: 0; }
  html, body { width: 1200px; height: 2526px; overflow: hidden; }
  body { background: var(--stage); font-family: "Poppins", sans-serif; color: var(--ink); position: relative; }

  .banner { position: absolute; left: 157px; top: 217px; width: 910px; height: 2141px; background: var(--paper); overflow: hidden; }
  .banner > * { position: absolute; }

  .brand { top: 72px; left: 0; width: 100%; text-align: center; font-weight: 800; font-size: 66px; line-height: 1; letter-spacing: 2px; color: var(--ink); }

  .headline-top { top: 272px; left: 0; width: 100%; text-align: center; font-family: "Anton", sans-serif; font-size: 146px; line-height: 1; color: var(--brand-blue); letter-spacing: 1px; }
  .headline-main { top: 401px; left: 0; width: 100%; text-align: center; font-weight: 800; font-size: 92px; line-height: 1; letter-spacing: -2px; }
  .headline-sub { top: 496px; left: 18px; width: 100%; text-align: center; font-weight: 800; font-size: 56px; line-height: 1; letter-spacing: 0.38em; color: var(--brand-blue); }

  .ribbon { top: 570px; left: 65px; width: 778px; height: 76px; }
  .ribbon-text { top: 570px; left: 139px; width: 631px; height: 62px; display: flex; align-items: center; justify-content: center; color: #fff; font-weight: 700; font-size: 29px; letter-spacing: 0; }

  .team-art { top: 663px; left: 65px; width: 778px; height: 577px; border-radius: 389px 389px 0 0; background: radial-gradient(ellipse at 50% 40%, var(--art-top) 0%, var(--art-mid) 55%, var(--art-low) 100%); border-bottom: 2px solid #5b8fc7; }

  .discover { top: 1278px; left: 14px; width: 100%; text-align: center; font-weight: 800; font-size: 54px; line-height: 1; letter-spacing: 0.32em; color: var(--brand-blue); }
  .discover-copy { top: 1348px; left: 0; width: 100%; text-align: center; font-weight: 700; font-size: 38px; line-height: 49px; }

  .services { top: 1486px; left: 69px; width: 772px; height: 303px; border-radius: 22px; overflow: hidden; display: grid; grid-template-columns: 258px 256px 258px; }
  .service { background: var(--panel-light); display: flex; flex-direction: column; align-items: center; padding-top: 32px; }
  .service.is-featured { background: var(--panel-mid); }
  .service-icon { width: 148px; height: 148px; }
  .service-name { margin-top: 14px; font-weight: 700; font-size: 37px; line-height: 44px; text-align: center; }

  .contact-title { top: 1858px; left: 71px; font-size: 62px; line-height: 60px; }
  .contact-title .light { font-weight: 400; display: block; }
  .contact-title .bold { font-weight: 800; display: block; }
  .contact-phone { top: 1855px; left: 313px; display: flex; align-items: center; gap: 12px; font-weight: 800; font-size: 56px; line-height: 1; letter-spacing: 1px; }
  .contact-web { top: 1926px; left: 316px; display: flex; align-items: center; gap: 10px; font-weight: 600; font-size: 30px; line-height: 1; }

  .footer { top: 2007px; left: 0; width: 100%; height: 134px; background: var(--footer); color: #fff; display: flex; align-items: flex-start; padding: 22px 0 0 83px; font-size: 41px; line-height: 1.2; }
  .footer .follow { font-weight: 400; }
  .footer .social-dot { width: 38px; height: 38px; border-radius: 50%; background: var(--brand-blue); margin: 9px 20px 0 28px; }
  .footer .handle { font-weight: 700; font-size: 43px; }
</style>
</head>
<body>
  <main class="banner">
    <div class="brand">QUELLA STAFFING</div>

    <h1 class="headline-top">HEALTHCARE</h1>
    <div class="headline-main">RECRUITMENT</div>
    <div class="headline-sub">AGENCY</div>

    <svg class="ribbon" viewBox="0 0 778 76" aria-hidden="true">
      <polygon points="0,76 66,76 66,18 0,18 30,47" fill="var(--brand-blue)"/>
      <polygon points="778,76 712,76 712,18 778,18 748,47" fill="var(--brand-blue)"/>
      <rect x="74" y="0" width="631" height="62" fill="var(--brand-blue)"/>
    </svg>
    <div class="ribbon-text">EMPOWERING YOUR NEXT CAREER MOVE</div>

    <div class="team-art" role="img" aria-label="Illustration of three healthcare professionals – a surgeon, a doctor with a clipboard and a nurse – in front of light blue leaves"></div>

    <div class="discover">DISCOVER</div>
    <p class="discover-copy">Tailored opportunities based on<br>your career preference</p>

    <section class="services">
      <div class="service">
        <svg class="service-icon" viewBox="0 0 148 148" aria-hidden="true">
          <circle cx="74" cy="74" r="72" fill="none" stroke="var(--ring)" stroke-width="3"/>
          <circle cx="74" cy="74" r="64" fill="var(--brand-blue)"/>
          <path d="M74 112 L40 78 C28 66 32 44 50 42 C61 41 69 47 74 55 C79 47 87 41 98 42 C116 44 120 66 108 78 Z" fill="#fff"/>
          <polyline points="36,75 58,75 64,64 72,88 80,70 86,75 112,75" fill="none" stroke="var(--brand-blue)" stroke-width="5" stroke-linejoin="round"/>
        </svg>
        <div class="service-name">Allied<br>health</div>
      </div>
      <div class="service is-featured">
        <svg class="service-icon" viewBox="0 0 148 148" aria-hidden="true">
          <circle cx="74" cy="74" r="72" fill="none" stroke="var(--ring)" stroke-width="3"/>
          <circle cx="74" cy="74" r="64" fill="var(--brand-blue)"/>
          <rect x="50" y="44" width="48" height="62" rx="6" fill="#fff"/>
          <rect x="62" y="38" width="24" height="12" rx="3" fill="#fff" stroke="var(--brand-blue)" stroke-width="3"/>
          <rect x="70" y="60" width="8" height="26" fill="var(--brand-blue)"/>
          <rect x="61" y="69" width="26" height="8" fill="var(--brand-blue)"/>
        </svg>
        <div class="service-name">Nursing</div>
      </div>
      <div class="service">
        <svg class="service-icon" viewBox="0 0 148 148" aria-hidden="true">
          <circle cx="74" cy="74" r="72" fill="none" stroke="var(--ring)" stroke-width="3"/>
          <circle cx="74" cy="74" r="64" fill="var(--brand-blue)"/>
          <circle cx="74" cy="74" r="37" fill="#fff"/>
          <rect x="66" y="52" width="16" height="44" fill="var(--brand-blue)"/>
          <rect x="52" y="66" width="44" height="16" fill="var(--brand-blue)"/>
        </svg>
        <div class="service-name">Medical</div>
      </div>
    </section>

    <div class="contact-title"><span class="light">GET IN</span><span class="bold">TOUCH</span></div>
    <div class="contact-phone">
      <svg width="46" height="46" viewBox="0 0 46 46" aria-hidden="true">
        <circle cx="23" cy="23" r="23" fill="var(--brand-blue)"/>
        <path d="M15 11 L20 11 L22 18 L19 21 C21 25 24 28 28 30 L31 27 L38 29 L38 34 C38 36 36 37 34 37 C22 36 12 26 11 15 C11 13 13 11 15 11 Z" fill="#fff"/>
      </svg>
      <span>9012 345 678</span>
    </div>
    <div class="contact-web">
      <svg width="40" height="40" viewBox="0 0 40 40" aria-hidden="true">
        <g fill="none" stroke="var(--brand-blue)" stroke-width="3">
          <circle cx="20" cy="20" r="17"/>
          <ellipse cx="20" cy="20" rx="7" ry="17"/>
          <line x1="3" y1="20" x2="37" y2="20"/>
          <path d="M6 11 H34 M6 29 H34"/>
        </g>
      </svg>
      <span>www.quellastaffing.com.au</span>
    </div>

    <footer class="footer">
      <span class="follow">Follow us on</span>
      <span class="social-dot" aria-hidden="true"></span>
      <span class="handle">@quellastaffing</span>
    </footer>
  </main>
</body>
</html>
```